High-end construction company needs a business card design

We need a modern looking business card that draws people in, is memorable and looks so good people will want to sick it on their fridges.
On the first side what is needed are:
Logo
My name - Tomasz Brelwik
Title - Managing Director
Website - www.varkelt.co.uk
Email - tomasz@varkelt.co.uk
Telephone - 020 5194 6281
Mobile - 07845139072
On the back side was is needed is a list of all the services we provide:
-Kitchen Renovations
-Bathroom Renovations
-House Renovations
-Garage Conversions
-Extensions
-Loft Conversions
-Conservatories
-Carpentry
-Tiling
-Electrical
-Plumbing & Heating
-Bricklaying
-Landscaping
-Decorating
-Plastering
We would like the colours to be the same shades as on the logo with grey or black for the words.
Target Market(s)
Anyone who needs building work done
Contact Information for Business Card
This business card is for a construction company which strives to deliver excellent service and quality.
The look and feel of the card should represent this.
Requirements
Must have
- On the first side what is needed are:
Logo
My name - Tomasz Brelwik
Title - Managing Director
Website - www.varkelt.co.uk
Email - tomasz@varkelt.co.uk
Telephone - 020 5194 6281
Mobile - 07845139072
Nice to have
- Cool looking features

```html
<!DOCTYPE html>
<html lang="en">
<head>
<meta charset="utf-8">
<title>Varkelt Construction Ltd – Business Card</title>
<link href="https://fonts.googleapis.com/css2?family=Archivo:wght@800&family=Arimo:wght@400;700&display=swap" rel="stylesheet">
<style>
  :root {
    --bg: #2b2b2c;
    --card: #1d1e20;
    --card-pattern-top: #26272a;
    --green: #6cc23f;
    --green-dark: #4f9a35;
    --white: #f4f4f4;
    --rule: #6a6a6a;
  }
  * { box-sizing: border-box; margin: 0; padding: 0; }
  html, body {
    width: 1200px; height: 1108px; overflow: hidden;
    background: var(--bg);
  }
  .canvas {
    position: relative; width: 1200px; height: 1108px;
    display: flex; justify-content: center; align-items: center; gap: 70px;
  }
  .card {
    position: relative; width: 380px; height: 590px;
    background: var(--card); border-radius: 22px;
    box-shadow: 0 18px 40px rgba(0,0,0,.45);
    overflow: hidden;
    font-family: "Arimo", Arial, sans-serif;
  }

  /* Front */
  .card-front { display: flex; flex-direction: column; align-items: center; }
  .brand {
    margin-top: 120px; display: flex; flex-direction: column; align-items: center; gap: 8px;
  }
  .brand-name {
    font-family: "Archivo", "Arial Black", sans-serif; font-weight: 800;
    color: var(--green); font-size: 64px; letter-spacing: 2px; line-height: 1;
  }
  .brand-sub {
    font-family: "Archivo", "Arial Black", sans-serif; font-weight: 800;
    color: var(--green); font-size: 17px; letter-spacing: 5px;
  }
  .person { margin-top: 150px; text-align: center; }
  .person-name {
    font-family: "Archivo", "Arial Black", sans-serif; font-weight: 800;
    color: var(--green); font-size: 25px; text-transform: uppercase; letter-spacing: .5px;
  }
  .person-title {
    color: var(--green-dark); font-size: 15px; text-transform: uppercase; letter-spacing: 1px; margin-top: 4px;
  }
  .icon-row {
    display: flex; align-items: center; gap: 8px; margin-top: 22px;
  }
  .icon-row .rule { width: 36px; height: 1px; background: var(--rule); }
  .icon {
    width: 30px; height: 30px; border-radius: 6px; background: var(--green);
    display: flex; align-items: center; justify-content: center;
  }
  .icon svg { width: 18px; height: 18px; }
  .contact-list {
    list-style: none; text-align: center; margin-top: 14px;
    color: var(--white); font-size: 17px; line-height: 24px;
  }

  /* Back */
  .pattern-area {
    position: absolute; left: 0; top: 0; width: 100%; height: 320px;
    background: linear-gradient(180deg, var(--card-pattern-top) 0%, var(--card) 100%);
  }
  .services {
    position: absolute; left: 0; right: 0; top: 330px;
    list-style: none; text-align: center;
    color: var(--green); font-size: 18px; line-height: 22px; text-transform: uppercase; letter-spacing: .3px;
  }
</style>
</head>
<body>
<main class="canvas">

  <section class="card card-front" aria-label="Business card front">
    <div class="brand">
      <span class="brand-name">VARKELT</span>
      <span class="brand-sub">CONSTRUCTION LTD</span>
    </div>

    <div class="person">
      <h1 class="person-name">Tomasz Brelwik</h1>
      <p class="person-title">Managing Director</p>
    </div>

    <div class="icon-row">
      <span class="rule"></span>
      <span class="icon" aria-label="Telephone">
        <svg viewBox="0 0 24 24"><path fill="#1d1e20" d="M6.6 10.8a15 15 0 0 0 6.6 6.6l2.2-2.2a1 1 0 0 1 1-.25 11.4 11.4 0 0 0 3.6.57 1 1 0 0 1 1 1V20a1 1 0 0 1-1 1A17 17 0 0 1 3 4a1 1 0 0 1 1-1h3.5a1 1 0 0 1 1 1c0 1.25.2 2.45.57 3.57a1 1 0 0 1-.25 1z"/></svg>
      </span>
      <span class="icon" aria-label="Mobile">
        <svg viewBox="0 0 24 24"><rect x="6" y="2" width="12" height="20" rx="2" fill="#1d1e20"/><rect x="8" y="5" width="8" height="12" fill="#6cc23f"/></svg>
      </span>
      <span class="icon" aria-label="Email">
        <svg viewBox="0 0 24 24"><rect x="2" y="5" width="20" height="14" rx="1.5" fill="#1d1e20"/><path d="M3 6l9 7 9-7" stroke="#6cc23f" stroke-width="1.6" fill="none"/></svg>
      </span>
      <span class="icon" aria-label="Website">
        <svg viewBox="0 0 24 24"><circle cx="12" cy="12" r="9" fill="#1d1e20"/><path d="M3 12h18M12 3c3 3 3 15 0 18M12 3c-3 3-3 15 0 18" stroke="#6cc23f" stroke-width="1.4" fill="none"/></svg>
      </span>
      <span class="rule"></span>
    </div>

    <ul class="contact-list">
      <li>020 5194 6281</li>
      <li>07845139072</li>
      <li>tomasz@varkelt.co.uk</li>
      <li>www.varkelt.co.uk</li>
    </ul>
  </section>

  <section class="card card-back" aria-label="Business card back">
    <div class="pattern-area" role="img" aria-label="Faint repeating pattern of the company house and building symbol"></div>
    <ul class="services">
      <li>Kitchen Renovations</li>
      <li>Bathroom Renovations</li>
      <li>Extensions | Loft Conversions</li>
      <li>Conservatories | Carpentry</li>
      <li>House Renovations</li>
      <li>Garage Conversions</li>
      <li>Tiling | Electrical</li>
      <li>Plumbing &amp; Heating</li>
      <li>Bricklaying | Landscaping</li>
      <li>Decorating | Plastering</li>
    </ul>
  </section>

</main>
</body>
</html>
```